Quality Monitoring Company Needs a New Site

We are an established company that has a fair number of clients but the site lacks current design standards that we'd like to keep up with. We'd like to mimic the same style of the site on plinkora.com, vetrumo.com, https://brindlecoffer.com/, etc. We'd also like to make sure the designer understands SEO Silos and how it effects the design elements. Attached is the structure that I'd like to follow for the pages. You don't need to design every single sub-page because they'll probably be fairly similar; however, I want to see at least 1 each. Please use the content on our current site for filler areas. Please try to do a good job of understanding what we do so you can use your best judgement on what is needed to be successful. Use our color scheme and the logo should be the side view but I included the AI just in case.
Updates

I am narrowing down on the field of designs that I have received. There are a lot of similarities between the designs I like and don't like. I'd also like to ensure that some of the inner pages get done in the next 5 days so I can see the creativity that is there as well. That is probably what is next -- getting a few inner pages completed so I can see what you can come up with (not based on our current website) because the current "front pages" are all so good and so close.

Industry/Entity Type

Telecommunications

Colors

Designer to choose colors to be used in the design.

Requirements
Must have
• SEO Silo Look and Feel
• Current Colors
Should not have
• No stockphotos whatsoever. NONE.

```html
<!DOCTYPE html>
<html lang="en">
<head>
<meta charset="utf-8">
<title>Tallyverse – Pricing</title>
<link href="https://fonts.googleapis.com/css2?family=Poppins:wght@400;500;600;700&display=swap" rel="stylesheet">
<style>
:root{
  --navy:#0b2d57;
  --navy-deep:#002e5a;
  --sky:#00ade6;
  --page:#f5f7fb;
  --ring:#e3f0fd;
  --ring-soft:#eef6fd;
  --ink:#333d4a;
  --muted:#5f6670;
  --white:#ffffff;
  --figure-red:#e84648;
  --figure-dark:#2f3e5c;
}
*{box-sizing:border-box;margin:0;padding:0}
html,body{width:1200px;height:1124px;overflow:hidden}
body{font-family:'Poppins',sans-serif;background:var(--page);color:var(--ink);position:relative}
.abs{position:absolute}
.bg-rings{position:absolute;left:0;top:0;width:1200px;height:856px;overflow:hidden}
.brand{left:141px;top:68px;font-size:21px;font-weight:500;color:var(--navy);display:flex;align-items:center;gap:8px}
.brand-dot{width:14px;height:14px;border-radius:50%;background:var(--sky)}
.nav{top:78px;left:404px;display:flex;font-size:12px;color:var(--ink)}
.nav a{color:inherit;text-decoration:none;position:absolute;white-space:nowrap}
.nav a.active{color:var(--sky);font-weight:600}
.phone-badge{left:904px;top:64px;width:38px;height:38px;border-radius:50%;background:var(--sky);display:flex;align-items:center;justify-content:center}
.phone-number{left:950px;top:72px;font-size:14px;font-weight:700;color:var(--navy);letter-spacing:.3px}
.page-title{left:0;width:1200px;top:166px;text-align:center;font-size:31px;font-weight:700;color:var(--navy)}
.title-rule{left:583px;top:219px;width:35px;height:2px;background:var(--sky)}
.tab-active{left:431px;top:248px;width:127px;height:32px;border-radius:16px;background:var(--sky);color:var(--white);font-size:14px;font-weight:600;display:flex;align-items:center;justify-content:center;box-shadow:0 6px 14px rgba(0,173,230,.25)}
.tab{left:583px;top:255px;font-size:14px;font-weight:600;color:var(--navy)}
.field-label{top:331px;width:211px;text-align:center;font-size:10px;font-weight:600;color:var(--navy)}
.field{top:354px;width:211px;height:32px;border-radius:12px;background:var(--white);box-shadow:0 4px 12px rgba(20,50,90,.06);display:flex;align-items:center;justify-content:center;font-size:12px;color:var(--muted)}
.starting{left:0;width:1200px;top:420px;text-align:center;font-size:8.5px;color:var(--navy)}
.stat{top:451px;width:130px;text-align:center}
.stat-label{font-size:10px;font-weight:600;color:var(--navy)}
.stat-value{font-size:20px;font-weight:700;color:var(--sky);line-height:1.2}
.stat-note{font-size:6.5px;color:var(--muted)}
.total-box{left:659px;top:442px;width:112px;height:49px;border-radius:3px;background:var(--sky);color:var(--white);text-align:center;padding-top:6px}
.total-box b{display:block;font-size:19px;font-weight:700;line-height:1}
.total-box span{font-size:9.5px;font-weight:600}
.btn-dark{left:523px;top:533px;width:155px;height:35px;border-radius:18px;background:var(--navy);color:var(--white);font-size:13px;letter-spacing:.4px;display:flex;align-items:center;justify-content:center}
.figure{border-radius:40px 40px 8px 8px}
.figure-left{left:150px;top:198px;width:140px;height:353px;background:linear-gradient(180deg,#f0b08f 0%,var(--figure-red) 30%,var(--figure-dark) 60%,#1f2d45 100%);opacity:.9}
.figure-right{left:915px;top:198px;width:140px;height:353px;background:linear-gradient(180deg,#f2c7a0 0%,var(--figure-red) 25%,#3a4046 60%,#2c3136 100%);opacity:.9}
.cta-card{left:203px;top:618px;width:794px;height:148px;border-radius:74px;background:var(--white);box-shadow:0 10px 30px rgba(20,50,90,.06)}
.cta-text{left:203px;top:652px;width:794px;text-align:center;font-size:11.3px;line-height:19px;color:var(--muted)}
.btn-sky{left:501px;top:700px;width:198px;height:35px;border-radius:18px;background:var(--sky);color:var(--white);font-size:13.5px;letter-spacing:.3px;display:flex;align-items:center;justify-content:center}
.footer{left:0;top:856px;width:1200px;height:268px;background:var(--navy-deep);color:var(--white)}
.footer-heading{font-size:17px;font-weight:700;color:var(--sky)}
.footer-links{font-size:11.5px;line-height:20.3px}
.footer-contact{font-size:13px;line-height:23px}
.footer-brand{left:932px;top:95px;width:128px;text-align:center;font-size:20px;font-weight:500;color:var(--white)}
.footer-rule{left:139px;top:222px;width:919px;height:1px;background:rgba(255,255,255,.18)}
.copyright{left:0;top:237px;width:1200px;text-align:center;font-size:12.5px}
</style>
</head>
<body>

<svg class="bg-rings" viewBox="0 0 1200 856" aria-hidden="true">
  <circle cx="1017" cy="155" r="390" fill="var(--ring-soft)" opacity=".7"/>
  <circle cx="1017" cy="155" r="283" fill="var(--ring)"/>
  <circle cx="1017" cy="155" r="212" fill="var(--page)"/>
</svg>

<header>
  <div class="abs brand"><span class="brand-dot"></span>Tallyverse</div>
  <nav class="abs nav">
    <a style="left:0">Home</a>
    <a style="left:58px">Services</a>
    <a style="left:132px">Industries</a>
    <a class="active" style="left:213px">Pricing</a>
    <a style="left:282px">Team</a>
    <a style="left:339px">Blog</a>
    <a style="left:389px">Contact Us</a>
  </nav>
  <div class="abs phone-badge">
    <svg width="14" height="14" viewBox="0 0 24 24"><path fill="#fff" d="M6.6 10.8a15.1 15.1 0 0 0 6.6 6.6l2.2-2.2a1 1 0 0 1 1-.25 11.4 11.4 0 0 0 3.6.57 1 1 0 0 1 1 1V20a1 1 0 0 1-1 1A17 17 0 0 1 3 4a1 1 0 0 1 1-1h3.5a1 1 0 0 1 1 1c0 1.25.2 2.45.57 3.57a1 1 0 0 1-.25 1z"/></svg>
  </div>
  <div class="abs phone-number">555-014-2270</div>
</header>

<main>
  <div class="abs figure figure-left" role="img" aria-label="Illustration of a woman in a red top holding an open laptop"></div>
  <div class="abs figure figure-right" role="img" aria-label="Illustration of a man in a red sweater carrying a folder"></div>

  <h1 class="abs page-title">Pricing</h1>
  <div class="abs title-rule"></div>

  <div class="abs tab-active">Calculator</div>
  <div class="abs tab">Pricing/ Mins With Details</div>

  <div class="abs field-label" style="left:381px"># of Calls / Month*</div>
  <div class="abs field-label" style="left:607px">Average Call Length*</div>
  <div class="abs field" style="left:381px">5,000</div>
  <div class="abs field" style="left:607px">6</div>

  <p class="abs starting">Starting at $.20 per call minute</p>

  <div class="abs stat" style="left:418px">
    <div class="stat-label">Total Minutes</div>
    <div class="stat-value">30,000</div>
    <div class="stat-note">30,000 minutes minimum</div>
  </div>
  <div class="abs stat" style="left:527px">
    <div class="stat-label">Cost Per Min</div>
    <div class="stat-value">$0.20</div>
  </div>
  <div class="abs total-box"><b>$6,000</b><span>+ $999 setup fee</span></div>

  <div class="abs btn-dark">GET STARTED</div>

  <section>
    <div class="abs cta-card"></div>
    <p class="abs cta-text">Contact us today to learn more! We will have someone contact you to discuss pricing, show you a demonstration<br>of our system, and answer all of your questions. We look forward to discussing your quality processes!</p>
    <div class="abs btn-sky">CONTACT US NOW</div>
  </section>
</main>

<footer class="abs footer">
  <div class="abs footer-heading" style="left:139px;top:55px">Quick Links</div>
  <div class="abs footer-links" style="left:139px;top:89px">Home<br>Services<br>System Details<br>Pricing</div>
  <div class="abs footer-links" style="left:294px;top:89px">Team<br>Blog<br>Contact Us<br>Login</div>

  <div class="abs footer-heading" style="left:460px;top:55px">Contact Us</div>
  <svg class="abs" style="left:462px;top:95px" width="11" height="15" viewBox="0 0 24 32"><path fill="#fff" d="M12 0C5.4 0 0 5.4 0 12c0 9 12 20 12 20s12-11 12-20C24 5.4 18.6 0 12 0zm0 17a5 5 0 1 1 0-10 5 5 0 0 1 0 10z"/></svg>
  <div class="abs footer-contact" style="left:480px;top:90px">4410 Harlow Ave.<br>Fairhaven, CA 90210</div>
  <svg class="abs" style="left:660px;top:96px" width="14" height="14" viewBox="0 0 24 24"><path fill="#fff" d="M6.6 10.8a15.1 15.1 0 0 0 6.6 6.6l2.2-2.2a1 1 0 0 1 1-.25 11.4 11.4 0 0 0 3.6.57 1 1 0 0 1 1 1V20a1 1 0 0 1-1 1A17 17 0 0 1 3 4a1 1 0 0 1 1-1h3.5a1 1 0 0 1 1 1c0 1.25.2 2.45.57 3.57a1 1 0 0 1-.25 1z"/></svg>
  <div class="abs footer-contact" style="left:682px;top:90px">555-014-2270</div>
  <svg class="abs" style="left:660px;top:132px" width="15" height="11" viewBox="0 0 24 18"><path fill="#fff" d="M0 0h24v18H0z"/><path fill="none" stroke="#002e5a" stroke-width="2" d="M1 1l11 9 11-9"/></svg>
  <div class="abs footer-contact" style="left:682px;top:125px">Hello@Tallyverse.com</div>

  <div class="abs footer-brand">Tallyverse</div>

  <div class="abs footer-rule"></div>
  <div class="abs copyright">Copyright © 2019 TALLYVERSE. All Rights Reserved.</div>
</footer>

</body>
</html>
```